Business Cards - Brightpath Horizon

need to design unique business card for my mortgage business. I need to design credit card style business card for my business or any unique idea that you might have

Target Market(s)

Home Loan customers

Industry/Entity Type

Mortgage Brokerage

Contact Information for Business Card

please design credit card style or very unique style business card

Colors

Designer to choose colors to be used in the design.

Requirements
Must have
• Name
• position
• Phone number
• fax number
• email address
• website address
• social media address
• All above fields will be provided once design in finalised

```html
<!DOCTYPE html>
<html lang="en">
<head>
<meta charset="utf-8">
<title>Brightpath Horizon – Business Card</title>
<link rel="stylesheet" href="https://fonts.googleapis.com/css2?family=Tinos:ital,wght@0,400;0,700;1,400&family=Share+Tech+Mono&display=swap">
<style>
  :root {
    --stage: #141414;
    --card-deep: #1d4fd6;
    --card-mid: #1f74e6;
    --card-light: #3fb4f2;
    --ink: #ffffff;
    --accent: #f28a1e;
    --tree-tint: rgba(160, 215, 255, 0.32);
    --tree-fade: rgba(160, 215, 255, 0);
  }
  * { margin: 0; padding: 0; box-sizing: border-box; }
  html, body {
    width: 1200px;
    height: 901px;
    overflow: hidden;
    background: var(--stage);
  }
  .business-card {
    position: absolute;
    left: 100px;
    top: 133px;
    width: 1000px;
    height: 635px;
    border-radius: 30px;
    overflow: hidden;
    background: linear-gradient(125deg, var(--card-deep) 0%, var(--card-mid) 55%, var(--card-light) 100%);
    color: var(--ink);
    font-family: "Tinos", "Times New Roman", serif;
  }
  .tree-artwork {
    position: absolute;
    left: 620px;
    top: 0;
    width: 380px;
    height: 500px;
    background: radial-gradient(closest-side, var(--tree-tint) 0%, rgba(160, 215, 255, 0.12) 60%, var(--tree-fade) 100%);
  }
  .brand {
    position: absolute;
    left: 55px;
    top: 130px;
  }
  .brand-name {
    font-size: 46px;
    font-weight: 400;
    line-height: 1;
    color: var(--ink);
    white-space: nowrap;
  }
  .brand-tagline {
    margin-top: 14px;
    font-size: 22px;
    font-style: italic;
    color: var(--accent);
    white-space: nowrap;
  }
  .social-links {
    position: absolute;
    left: 755px;
    top: 144px;
    display: flex;
    gap: 10px;
  }
  .social-dot {
    width: 40px;
    height: 40px;
    border-radius: 50%;
    background: var(--ink);
  }
  .card-number {
    position: absolute;
    left: 224px;
    top: 298px;
    font-family: "Share Tech Mono", monospace;
    font-size: 78px;
    letter-spacing: 6px;
    line-height: 1;
    white-space: nowrap;
  }
  .holder {
    position: absolute;
    right: 48px;
    top: 420px;
    text-align: right;
  }
  .holder-name {
    font-size: 33px;
    font-weight: 700;
    letter-spacing: 1px;
    line-height: 1.1;
  }
  .holder-role {
    font-size: 26px;
    line-height: 1.3;
  }
  .holder-address {
    margin-top: 16px;
    font-size: 24px;
    white-space: nowrap;
  }
  .holder-contacts {
    margin-top: 10px;
    font-size: 24px;
    white-space: nowrap;
  }
  .holder-contacts b { font-weight: 700; }
  .holder-contacts span + span { margin-left: 12px; }
</style>
</head>
<body>
  <main class="business-card">
    <div class="tree-artwork" role="img" aria-label="Faint silhouette of a leafy tree"></div>

    <div class="brand">
      <div class="brand-name">Brightpath Horizon</div>
      <div class="brand-tagline">Smart choice, Safe home</div>
    </div>

    <div class="social-links" aria-label="Social media links">
      <div class="social-dot"></div>
      <div class="social-dot"></div>
      <div class="social-dot"></div>
      <div class="social-dot"></div>
    </div>

    <div class="card-number">517 302 8846</div>

    <div class="holder">
      <div class="holder-name">DANIEL HARTLEY</div>
      <div class="holder-role">CEO/FOUNDER</div>
      <div class="holder-address">2140 Maple Ridge Road, Juneau, Alaska 99801</div>
      <div class="holder-contacts">
        <span><b>P:</b> 907 555 0143</span>
        <span><b>E:</b> mail@bphorizon.com</span>
        <span><b>W:</b> www.bphorizon.com</span>
      </div>
    </div>
  </main>
</body>
</html>
```